Healthcare and Professional IT Services Company need a redesigned business card

We are a IT Services company that targets small medical practices and professional business such as Attorneys, Accounts, Architects etc. We want to communicate a professional yet friendly image using recent logo redesign here on ArtHarbor. Like to see the colors blue and orange in the design. Must use the Tall Pine Computing as displayed in the new logo - then also want to incorporate the fish logo as well.

Target Market(s)

Small medical and professional services

Industry/Entity Type

It Company

Contact Information for Business Card

The usual stuff, place for name address phone website. Also maybe our tagline which is "hooked on technology"

Requirements
Must have
• My new logo and the fish somewhere on the card

```html
<!DOCTYPE html>
<html lang="en">
<head>
<meta charset="utf-8">
<title>Tall Pine Computing – Business Card</title>
<link rel="stylesheet" href="https://fonts.googleapis.com/css2?family=Open+Sans:wght@400;600&display=swap">
<style>
  :root {
    --backdrop: #e9e6e1;
    --card: #f4f4f4;
    --brand-blue: #2a9bd8;
    --brand-blue-light: #bfe2f5;
    --ink: #111111;
    --rule: #333333;
  }
  * { margin: 0; padding: 0; box-sizing: border-box; }
  html, body {
    width: 1200px;
    height: 902px;
    overflow: hidden;
    background: var(--backdrop);
    font-family: "Open Sans", Verdana, sans-serif;
  }
  .canvas {
    width: 1200px;
    height: 902px;
    display: flex;
    align-items: center;
    justify-content: center;
  }
  .business-card {
    width: 1000px;
    height: 572px;
    background: var(--card);
    box-shadow: 0 6px 24px rgba(0,0,0,0.18);
    display: flex;
    align-items: center;
    position: relative;
  }
  .brand-block {
    width: 470px;
    padding-left: 70px;
    display: flex;
    flex-direction: column;
    align-items: flex-start;
  }
  .mascot-area {
    width: 300px;
    height: 210px;
    border-radius: 50% 46% 40% 50%;
    background: radial-gradient(ellipse at 60% 45%, var(--brand-blue-light), #e6f3fa 70%, var(--card) 100%);
    margin-left: 40px;
    margin-bottom: 18px;
  }
  .brand-name {
    color: var(--brand-blue);
    font-weight: 600;
    font-size: 38px;
    line-height: 1.1;
    letter-spacing: -0.5px;
  }
  .divider {
    width: 2px;
    height: 330px;
    background: var(--rule);
    margin-right: 60px;
  }
  .contact-block {
    color: var(--ink);
  }
  .person-name {
    font-size: 36px;
    font-weight: 600;
    letter-spacing: 1.5px;
    margin-bottom: 40px;
  }
  .contact-list { list-style: none; }
  .contact-list li {
    display: flex;
    align-items: flex-start;
    font-size: 22px;
    font-weight: 600;
    letter-spacing: 1px;
    line-height: 30px;
  }
  .contact-icon {
    width: 20px;
    height: 20px;
    margin: 5px 8px 0 0;
    flex: none;
  }
</style>
</head>
<body>
<main class="canvas">
  <article class="business-card">
    <section class="brand-block">
      <div class="mascot-area" role="img" aria-label="Cartoon fish mascot illustration in blue outline"></div>
      <div class="brand-name">Tall Pine Computing</div>
    </section>
    <div class="divider"></div>
    <section class="contact-block">
      <h1 class="person-name">Colin Harrow</h1>
      <ul class="contact-list">
        <li>
          <svg class="contact-icon" viewBox="0 0 20 20" aria-hidden="true"><rect width="20" height="20" fill="#111"/><path d="M6 4 L8 4 L9 7 L7.5 8.5 Q9 11.5 11.5 12.5 L13 11 L16 12 L16 14 Q15 16 12.5 15.5 Q6 13 4.5 7 Q4.5 4.5 6 4 Z" fill="#fff"/></svg>
          <span>0400 512 690</span>
        </li>
        <li>
          <svg class="contact-icon" viewBox="0 0 20 20" aria-hidden="true"><rect width="20" height="20" fill="#111"/><circle cx="10" cy="10" r="6" fill="none" stroke="#fff" stroke-width="1.5"/><path d="M4 10 H16 M10 4 Q6.5 10 10 16 M10 4 Q13.5 10 10 16" fill="none" stroke="#fff" stroke-width="1.2"/></svg>
          <span>www.tallpinecomputing.com</span>
        </li>
        <li>
          <svg class="contact-icon" viewBox="0 0 20 20" aria-hidden="true"><rect width="20" height="20" fill="#111"/><path d="M10 16 Q5 10.5 5 8 A5 5 0 0 1 15 8 Q15 10.5 10 16 Z" fill="#fff"/><circle cx="10" cy="8" r="1.8" fill="#111"/></svg>
          <span>2208 Harbor Crest Way<br>Bay Point, CA 94100</span>
        </li>
      </ul>
    </section>
  </article>
</main>
</body>
</html>
```